Custom hot rod builder needs a website for launch of new business where he will build luxury garages

We need a website that gives a WOW first impression for "Summit Carports". This is a new business so photos are renderings but we need it to really attract a particular audience. Our initial business is custom hot rods so now we are building garages for them. These will be like luxury "homes" for cars! I will attach our new logo. Website needs to feel powerful and prestigious.

Target Market(s)

middle aged men, car enthusiasts

Industry/Entity Type

automotive, construction

Coding

Coded - Design and coding required

Number of Pages Required

2 page

Font styles to use
Serif

Colors
0054AA
0677BA
7BADD7
CADEEF
E8F1F8

Requirements
Must have
• a WOW factor. luxury. contact form.
Nice to have
• ?

```html
<!DOCTYPE html>
<html lang="en">
<head>
<meta charset="utf-8">
<title>Summit Carports</title>
<link href="https://fonts.googleapis.com/css2?family=Saira:wght@400;500;600;700&family=Open+Sans:wght@400;600;700&display=swap" rel="stylesheet">
<style>
:root{
  --blue-deep:#0054aa;
  --blue:#0677ba;
  --blue-soft:#7badd7;
  --blue-pale:#cadeef;
  --blue-mist:#e8f1f8;
  --ink:#1d2a3a;
  --text:#4a5563;
  --white:#ffffff;
  --grey-band:#efefef;
  --night:#14181e;
}
*{box-sizing:border-box;margin:0;padding:0}
html,body{width:1200px;height:4568px;overflow:hidden}
body{font-family:"Open Sans",Arial,sans-serif;color:var(--text);background:var(--white);position:relative}
.heading{font-family:"Saira",Arial,sans-serif;font-weight:500;letter-spacing:3px;text-transform:uppercase}
.body-copy{font-size:14px;line-height:24px}
.btn{display:inline-flex;align-items:center;justify-content:center;background:var(--blue-deep);color:var(--white);font-family:"Saira",Arial,sans-serif;font-weight:600;letter-spacing:1.5px;font-size:17px;text-transform:uppercase;text-decoration:none;box-shadow:0 6px 14px rgba(0,0,0,.3)}
.abs{position:absolute}

/* hero */
.hero{position:absolute;left:0;top:0;width:1200px;height:768px;overflow:hidden}
.hero-photo{position:absolute;inset:0;background:radial-gradient(ellipse at 50% 70%,#5b5048 0%,#2c2724 45%,#121212 100%)}
.hero-photo::after{content:"";position:absolute;inset:0;background:linear-gradient(180deg,rgba(0,0,0,.35),rgba(0,0,0,.15) 60%,rgba(0,0,0,.45))}
.brand{position:absolute;left:112px;top:30px;display:flex;align-items:center;gap:10px}
.brand-dot{width:14px;height:14px;border-radius:50%;background:var(--blue)}
.brand-name{font-family:"Saira",Arial,sans-serif;font-weight:600;font-size:20px;color:var(--white);letter-spacing:1px}
.nav{position:absolute;right:112px;top:38px;display:flex;gap:32px}
.nav a{color:var(--white);text-decoration:none;font-family:"Saira",Arial,sans-serif;font-size:15px;font-weight:500;letter-spacing:1px}
.nav a.active{border-bottom:2px solid var(--white);padding-bottom:4px}
.hero-title{position:absolute;left:0;width:1200px;top:268px;text-align:center;color:var(--white);font-size:52px;letter-spacing:6px}
.hero-copy{position:absolute;left:300px;width:600px;top:344px;text-align:center;color:var(--white);font-size:15px;line-height:24px}
.hero .btn{position:absolute;left:484px;top:440px;width:228px;height:58px}
.dots{position:absolute;left:0;width:1200px;top:718px;display:flex;justify-content:center;gap:6px}
.dots span{width:14px;height:14px;border:2px solid var(--white)}
.dots span.on{background:var(--white)}

/* about */
.about-eyebrow{left:112px;top:832px;color:var(--blue);font-size:22px;font-family:"Saira",Arial,sans-serif}
.about-title{left:112px;top:866px;font-size:48px;color:var(--ink)}
.about-copy{left:112px;top:944px;width:540px}
.about .btn{left:112px;top:1232px;width:220px;height:62px}
.about-mark{left:660px;top:860px;width:420px;height:420px;display:flex;align-items:center;justify-content:center;gap:18px}
.about-mark .mark-circle{width:56px;height:56px;border-radius:50%;background:var(--blue)}
.about-mark .mark-name{font-family:"Saira",Arial,sans-serif;font-weight:600;font-size:40px;color:var(--blue)}

/* advantages */
.advantages{position:absolute;left:0;top:1352px;width:1200px;height:640px;background:linear-gradient(180deg,#0d5aa6 0%,var(--blue-deep) 55%,#0a4f9a 100%)}
.advantages-title{position:absolute;left:0;width:1200px;top:92px;text-align:center;color:var(--white);font-size:46px}
.adv-card{position:absolute;top:184px;width:314px}
.adv-photo{height:264px;box-shadow:0 8px 16px rgba(0,0,0,.35)}
.adv-card h3{margin-top:26px;color:var(--white);font-size:19px;letter-spacing:1.5px}
.adv-card p{color:var(--blue-mist);font-size:14px;line-height:20px;margin-top:4px}

/* parking */
.parking-title{left:112px;top:2092px;width:460px;font-size:36px;line-height:46px;color:var(--blue-deep);letter-spacing:2px}
.parking-copy{left:112px;top:2200px;width:440px}
.photo-blue{left:600px;top:2072px;width:488px;height:404px;background:radial-gradient(ellipse at 50% 60%,#2aa6e8,#0b3a66 60%,#061a30)}
.photo-red{left:400px;top:2480px;width:688px;height:312px;background:linear-gradient(160deg,#2a2a2e,#141417 60%,#3a0d0d)}

/* choice */
.choice-frame{left:160px;top:2880px;width:480px;height:480px;border:3px solid var(--blue-soft)}
.photo-rod{left:112px;top:2912px;width:480px;height:408px;background:linear-gradient(135deg,#8a8478,#3c3a36 55%,#1e1d1b)}
.choice-title{left:640px;top:2984px;width:460px;font-size:34px;line-height:44px;letter-spacing:2px;color:var(--blue-deep)}
.choice-copy{left:640px;top:3104px;width:440px}
.explore{left:640px;top:3320px;color:var(--blue-deep);font-family:"Saira",Arial,sans-serif;font-weight:600;font-size:16px;letter-spacing:1px;text-decoration:none}

/* articles */
.articles{position:absolute;left:0;top:3540px;width:1200px;height:600px;background:var(--grey-band)}
.articles-title{position:absolute;left:0;width:1200px;top:80px;text-align:center;color:var(--blue-deep);font-size:46px}
.article-card{position:absolute;top:160px;width:292px;height:368px;box-shadow:0 10px 18px rgba(0,0,0,.35);overflow:hidden}
.article-card .art-photo{position:absolute;inset:0}
.article-card .art-photo::after{content:"";position:absolute;inset:0;background:linear-gradient(180deg,rgba(0,0,0,0) 45%,rgba(0,0,0,.75))}
.article-card h4{position:absolute;left:16px;right:16px;bottom:82px;color:var(--white);font-family:"Saira",Arial,sans-serif;font-weight:600;font-size:17px;letter-spacing:1px}
.article-card p{position:absolute;left:16px;right:16px;bottom:18px;color:var(--white);font-size:12px;line-height:18px}

/* footer */
.footer{position:absolute;left:0;top:4140px;width:1200px;height:428px;background:linear-gradient(180deg,#0a4f9f,var(--blue-deep))}
.foot-col{position:absolute;top:78px;color:var(--white)}
.foot-col h5{font-family:"Saira",Arial,sans-serif;font-weight:600;font-size:22px;letter-spacing:1.5px;text-transform:uppercase;margin-bottom:10px}
.foot-col h5::after{content:"";display:block;width:40px;height:2px;background:var(--white);margin-top:4px}
.foot-col ul{list-style:none}
.foot-col li{font-size:15px;line-height:24px}
.foot-label{font-weight:700;font-size:14px;letter-spacing:1px;margin-top:8px}
.foot-line{font-size:14px;line-height:22px;display:flex;align-items:center;gap:8px}
.news-field{margin-top:22px;width:288px;height:42px;border-radius:21px;background:var(--white);display:flex;align-items:center;justify-content:space-between;padding:0 6px 0 18px;color:#333;font-size:13px}
.news-field span.go{width:30px;height:30px;border-radius:50%;background:var(--blue-deep);display:flex;align-items:center;justify-content:center}
.socials{display:flex;gap:14px;margin-top:26px;margin-left:8px}
.socials span{width:38px;height:38px;border-radius:50%;border:2px solid var(--white)}
.copyright{position:absolute;left:0;bottom:0;width:1200px;height:64px;border-top:1px solid rgba(255,255,255,.25);display:flex;align-items:center;justify-content:center;color:var(--white);font-size:14px}
</style>
</head>
<body>

<header class="hero">
  <div class="hero-photo" role="img" aria-label="Interior of a luxury showroom garage with classic cars under warm lights"></div>
  <div class="brand"><span class="brand-dot"></span><span class="brand-name">Summit Carports</span></div>
  <nav class="nav">
    <a class="active" href="#">HOME</a><a href="#">ABOUT</a><a href="#">COMMUNITY</a><a href="#">EVENTS</a><a href="#">GARAGES</a><a href="#">LOCATIONS</a><a href="#">NEWS</a><a href="#">CONTACT</a>
  </nav>
  <h1 class="hero-title heading">Summit Carports</h1>
  <p class="hero-copy">Lorem ipsum dolor sit amet, consectetur adipiscing elit, sed do eiusmod tempor incididunt ut labore et dolore magna aliqua. Ut enim ad minim veniam, quis nostrud exercitation ullamco laboris nisi.<br>Ut enim ad minim veniam, quis nostrud sed.</p>
  <a class="btn" href="#">Get Started</a>
  <div class="dots"><span class="on"></span><span></span><span></span><span></span><span></span></div>
</header>

<section class="about">
  <p class="abs about-eyebrow">About</p>
  <h2 class="abs about-title heading">Summit Carports</h2>
  <p class="abs about-copy body-copy">Lorem ipsum dolor sit amet, consectetur adipiscing elit, sed do eiusmod tempor incididunt ut labore et dolore magna aliqua. Ut enim ad minim veniam, quis nostrud exercitation ullamco laboris nisi ut aliquip ex ea commodo consequat. Duis aute irure dolor in reprehenderit in voluptate velit esse cillum dolore eu fugiat nulla pariatur. Excepteur sint occaecat cupidatat non proident, sunt in culpa qui officia deserunt mollit anim id est laborum. Lorem ipsum dolor sit amet, consectetur adipiscing elit, sed do eiusmod tempor incididunt ut labore et dolore magna aliqua. Ut enim ad minim veniam, quis nostrud exercitation ullamco laboris nisi ut aliquip ex ea commodo consequat.</p>
  <a class="abs btn" href="#">Read More</a>
  <div class="abs about-mark"><span class="mark-circle"></span><span class="mark-name">Summit Carports</span></div>
</section>

<section class="advantages">
  <h2 class="advantages-title heading">Luxury Garage Advantages</h2>
  <article class="adv-card" style="left:112px">
    <div class="adv-photo" role="img" aria-label="Dark private garage with a parked classic car" style="background:linear-gradient(160deg,#3d4650,#1b2026)"></div>
    <h3 class="heading">Be a Property Owner</h3>
    <p>Lorem ipsum dolor sit amet, consectetur adipiscing elit, sed do eiusmod tempor incididunt ut labore et dolore magna aliqua.</p>
  </article>
  <article class="adv-card" style="left:440px">
    <div class="adv-photo" role="img" aria-label="Bright garage interior with colourful sports cars" style="background:linear-gradient(160deg,#6a6a5a,#8a7a30 50%,#2e2c26)"></div>
    <h3 class="heading">Express Yourself</h3>
    <p>Lorem ipsum dolor sit amet, consectetur adipiscing elit, sed do eiusmod tempor incididunt ut labore et dolore magna aliqua.</p>
  </article>
  <article class="adv-card" style="left:772px">
    <div class="adv-photo" role="img" aria-label="Garage with wooden ceiling beams and a vintage car" style="background:linear-gradient(160deg,#5a4636,#2a2420 60%,#7a1f1f)"></div>
    <h3 class="heading">Easy Come, Easy Go</h3>
    <p>Lorem ipsum dolor sit amet, consectetur adipiscing elit, sed do eiusmod tempor incididunt ut labore et dolore magna aliqua.</p>
  </article>
</section>

<section class="parking">
  <h2 class="abs parking-title heading">Taking Parking to the Next Level</h2>
  <p class="abs parking-copy body-copy">Lorem ipsum dolor sit amet, consectetur adipiscing elit, sed do eiusmod tempor incididunt ut labore et dolore magna aliqua. Ut enim ad minim veniam, quis nostrud exercitation ullamco laboris nisi ut aliquip ex ea commodo consequat. Duis aute irure dolor in reprehenderit in voluptate velit esse.</p>
  <div class="abs photo-blue" role="img" aria-label="Sports car in a blue lit futuristic garage"></div>
  <div class="abs photo-red" role="img" aria-label="Red sports car on a dark studio floor"></div>
</section>

<section class="choice">
  <div class="abs choice-frame"></div>
  <div class="abs photo-rod" role="img" aria-label="Black vintage hot rod parked in front of an old brick building"></div>
  <h2 class="abs choice-title heading">Your Choice When<br>Excellence Matters</h2>
  <p class="abs choice-copy body-copy">Lorem ipsum dolor sit amet, consectetur adipiscing elit, sed do eiusmod tempor incididunt ut labore et dolore magna aliqua. Ut enim ad minim veniam, quis nostrud exercitation ullamco laboris nisi ut aliquip ex ea commodo consequat. Duis aute irure dolor in reprehenderit in voluptate velit esse cillum dolore eu fugiat nulla pariatur. Excepteur sint occaecat cupidatat non proident, sunt in culpa qui officia deserunt mollit anim id est laborum.</p>
  <a class="abs explore" href="#">EXPLORE NOW →</a>
</section>

<section class="articles">
  <h2 class="articles-title heading">Our Latest Articles</h2>
  <article class="article-card" style="left:140px">
    <div class="art-photo" role="img" aria-label="Hot rod with pink flame paintwork" style="background:linear-gradient(160deg,#1f6a6a,#7a2a5a 60%,#1a1a1a)"></div>
    <h4>LOREM IPSUM DOLOR SIT</h4>
    <p>Lorem ipsum dolor sit amet, consectetur adipiscing elit, sed do eiusmod tempor incididunt ut labore et dolore magna aliqua.</p>
  </article>
  <article class="article-card" style="left:452px">
    <div class="art-photo" role="img" aria-label="Row of classic cars inside a showroom" style="background:linear-gradient(160deg,#6a4a3a,#3a2a24 60%,#1a1a1a)"></div>
    <h4>LOREM IPSUM DOLOR SIT</h4>
    <p>Lorem ipsum dolor sit amet, consectetur adipiscing elit, sed do eiusmod tempor incididunt ut labore et dolore magna aliqua.</p>
  </article>
  <article class="article-card" style="left:764px">
    <div class="art-photo" role="img" aria-label="Red sports car in a dark garage" style="background:linear-gradient(160deg,#2a2a2e,#5a1a1a 60%,#141414)"></div>
    <h4>LOREM IPSUM DOLOR SIT</h4>
    <p>Lorem ipsum dolor sit amet, consectetur adipiscing elit, sed do eiusmod tempor incididunt ut labore et dolore magna aliqua.</p>
  </article>
</section>

<footer class="footer">
  <div class="foot-col" style="left:112px">
    <h5>Quick Links</h5>
    <ul><li>Home</li><li>About</li><li>Community</li><li>Events</li><li>Garages</li><li>Locations</li><li>News</li><li>Contact</li></ul>
  </div>
  <div class="foot-col" style="left:304px">
    <h5>About</h5>
    <ul><li>Community</li><li>Garages</li><li>Locations</li><li>Reviews</li></ul>
  </div>
  <div class="foot-col" style="left:504px">
    <h5>Contact Us</h5>
    <p class="foot-label">ADDRESS</p>
    <p class="foot-line">
      <svg width="12" height="16" viewBox="0 0 12 16"><path d="M6 0a6 6 0 0 0-6 6c0 4.5 6 10 6 10s6-5.5 6-10a6 6 0 0 0-6-6zm0 8.5A2.5 2.5 0 1 1 6 3.5a2.5 2.5 0 0 1 0 5z" fill="#fff"/></svg>
      Lorem ipsum dolor sit amet</p>
    <p class="foot-label">PHONE</p>
    <p class="foot-line">
      <svg width="14" height="14" viewBox="0 0 24 24"><path d="M6.6 10.8a15 15 0 0 0 6.6 6.6l2.2-2.2a1 1 0 0 1 1-.25 11.4 11.4 0 0 0 3.6.57 1 1 0 0 1 1 1V20a1 1 0 0 1-1 1A17 17 0 0 1 3 4a1 1 0 0 1 1-1h3.5a1 1 0 0 1 1 1c0 1.25.2 2.45.57 3.57a1 1 0 0 1-.25 1z" fill="#fff"/></svg>
      +1 555 014 2290</p>
    <p class="foot-label">EMAIL</p>
    <p class="foot-line">
      <svg width="16" height="12" viewBox="0 0 16 12"><rect x="0.5" y="0.5" width="15" height="11" fill="none" stroke="#fff"/><path d="M1 1l7 6 7-6" fill="none" stroke="#fff"/></svg>
      info@summitcarports.com</p>
  </div>
  <div class="foot-col" style="left:812px">
    <h5>Newsletter</h5>
    <p class="foot-line" style="width:280px">Lorem ipsum dolor sit amet, consectetur adipiscing elit, sed do eiusmod tempor</p>
    <div class="news-field">Enter Email
      <span class="go"><svg width="12" height="12" viewBox="0 0 12 12"><path d="M2 6h8M7 3l3 3-3 3" stroke="#fff" stroke-width="1.6" fill="none"/></svg></span>
    </div>
    <div class="socials"><span></span><span></span><span></span></div>
  </div>
  <div class="copyright">© 2023. All Rights Reserved</div>
</footer>

</body>
</html>
```